Largest women's organization in New Hampshire needs a new graphic for their Facebook, Twitter and LI

Our organization is celebrating its 10th anniversary and we are the largest organization in New Hampshire for personal and professional development, businesses resources, networking and fun. Our "vibe" is one of community, fun, polished professionalism, feminity and lots of motivation and inspiration. We like quotes like "she believed she could so she did" and "stimulate your mind, nurture your soul" which is kind of our tag line. Our colors are pink, black, white and lime green. We host a lot of events with the biggest being the NH Larkridge Summit Days. Our website is www.larkridgeforum.com / https://www.frendlio.com/LarkridgeCircleForum/?ref=bookmarks

```html
<!DOCTYPE html>
<html lang="en">
<head>
<meta charset="utf-8">
<title>Larkridge Circle Forum – Banner</title>
<link rel="stylesheet" href="https://fonts.googleapis.com/css2?family=Great+Vibes&family=Allura&family=Open+Sans:wght@400;600&display=swap">
<style>
  :root {
    --lavender: #b59fca;
    --mist: #e3e3e3;
    --white: #ffffff;
    --navy: #2d2b6e;
    --violet: #8a56a8;
    --orchid: #9a6cb3;
    --ink: #222222;
    --pink: #e6378f;
    --stage-dark: #2a1f2c;
    --stage-warm: #6b4a55;
    --portrait-light: #d8d0bf;
    --portrait-dark: #4d4250;
    --crowd-warm: #c98c96;
    --crowd-dark: #4a3a44;
  }
  html, body {
    margin: 0;
    padding: 0;
    overflow: hidden;
    background: var(--white);
  }
  .banner {
    position: relative;
    width: 1200px;
    height: 400px;
    overflow: hidden;
    background: var(--white);
    font-family: "Open Sans", sans-serif;
  }
  .banner__backdrop {
    position: absolute;
    inset: 0;
  }
  .brand {
    position: absolute;
    left: 176px;
    top: 46px;
    width: 230px;
    display: flex;
    align-items: center;
    gap: 10px;
  }
  .brand__dot {
    flex: none;
    width: 26px;
    height: 26px;
    border-radius: 50%;
    background: var(--pink);
  }
  .brand__name {
    margin: 0;
    font-family: "Great Vibes", cursive;
    font-weight: 400;
    font-size: 38px;
    line-height: 0.95;
    color: var(--ink);
  }
  .quote {
    position: absolute;
    left: 148px;
    top: 180px;
    width: 270px;
    height: 170px;
    margin: 0;
  }
  .quote span {
    position: absolute;
    white-space: nowrap;
  }
  .quote__she {
    left: 82px;
    top: 0;
    font-family: "Allura", cursive;
    font-size: 52px;
    color: var(--violet);
  }
  .quote__believed {
    left: 20px;
    top: 30px;
    font-family: "Allura", cursive;
    font-size: 58px;
    color: var(--navy);
  }
  .quote__could {
    left: 0;
    top: 92px;
    font-family: "Open Sans", sans-serif;
    font-size: 20px;
    color: var(--violet);
    letter-spacing: -0.3px;
  }
  .quote__did {
    left: 72px;
    top: 100px;
    font-family: "Allura", cursive;
    font-size: 62px;
    color: var(--navy);
  }
  .tagline {
    position: absolute;
    left: 700px;
    top: 306px;
    width: 410px;
    margin: 0;
    font-family: "Great Vibes", cursive;
    font-weight: 400;
    font-size: 38px;
    line-height: 1.05;
    color: var(--orchid);
    text-align: right;
  }
  .tagline__line {
    display: block;
  }
  .tagline__line--first {
    padding-right: 86px;
  }
</style>
</head>
<body>
  <main class="banner">
    <svg class="banner__backdrop" width="1200" height="400" viewBox="0 0 1200 400" aria-hidden="false">
      <defs>
        <linearGradient id="stage-tone" x1="0" y1="0" x2="1" y2="1">
          <stop offset="0" stop-color="var(--stage-dark)"/>
          <stop offset="0.6" stop-color="var(--stage-warm)"/>
          <stop offset="1" stop-color="var(--stage-dark)"/>
        </linearGradient>
        <linearGradient id="portrait-tone" x1="0" y1="0" x2="0" y2="1">
          <stop offset="0" stop-color="var(--portrait-light)"/>
          <stop offset="1" stop-color="var(--portrait-dark)"/>
        </linearGradient>
        <linearGradient id="crowd-tone" x1="0" y1="0" x2="1" y2="1">
          <stop offset="0" stop-color="var(--crowd-warm)"/>
          <stop offset="1" stop-color="var(--crowd-dark)"/>
        </linearGradient>
      </defs>
      <rect class="band-lavender" x="0" y="0" width="134" height="400" fill="var(--lavender)"/>
      <rect class="panel-mist" x="134" y="0" width="400" height="400" fill="var(--mist)"/>
      <circle class="panel-curve" cx="650" cy="200" r="240" fill="var(--white)"/>
      <path class="photo-stage" role="img" aria-label="Photo of two women in conversation on a lit event stage, audience at tables in front"
            fill="url(#stage-tone)"
            d="M896,172 C 820,64 712,16 626,16 C 524,16 442,100 442,200 C 442,300 524,384 626,384 C 724,384 806,292 896,172 Z"/>
      <path class="photo-portrait" role="img" aria-label="Photo of the organisation's founder posing with a guest speaker"
            fill="url(#portrait-tone)"
            d="M896,172 C 828,122 774,80 774,30 L774,0 L1006,0 L1006,30 C1006,80 962,122 896,172 Z"/>
      <path class="photo-crowd" role="img" aria-label="Photo of women networking around tables at a conference luncheon"
            fill="url(#crowd-tone)"
            d="M898,176 C 958,110 1020,80 1070,80 C 1135,80 1182,130 1182,196 C 1182,262 1135,312 1070,312 C 1020,312 958,262 898,176 Z"/>
    </svg>

    <div class="brand">
      <span class="brand__dot"></span>
      <p class="brand__name">Larkridge Circle Forum</p>
    </div>

    <p class="quote">
      <span class="quote__she">She</span>
      <span class="quote__believed">believed</span>
      <span class="quote__could">she could so</span>
      <span class="quote__did">she Did</span>
    </p>

    <p class="tagline">
      <span class="tagline__line tagline__line--first">Stimulate Your</span>
      <span class="tagline__line">Mind, Nurture Your Soul</span>
    </p>
  </main>
</body>
</html>
```